IT Company requires new Business Card design.

Over the years we have had a few different business card designs. We are now due for new cards across the board for all staff. We felt this would be a good time to start fresh with a new design. Our traditional card simply had our details on the front, and a list of services on the back. We don't particularly need the list of services, we have had cards where the only thing on the rear of the card was our logo.
Feel free to be creative, we would like our tag line "Complete IT Management" to appear at some point, doesn't necessarily have to be with the logo.
I have attached samples and drafts of various previous cards we have used over the years.

```html
<!DOCTYPE html>
<html lang="en">
<head>
<meta charset="utf-8">
<title>Corvale Networking – Business Card</title>
<link href="https://fonts.googleapis.com/css2?family=Source+Sans+3:wght@400;600;700&display=swap" rel="stylesheet">
<style>
  :root {
    --backdrop: #dcd8d3;
    --card-white: #ffffff;
    --slate: #627483;
    --slate-dark: #4f5e6b;
    --ink: #4a4f55;
    --rule-dark: #3f444a;
    --light-text: #ffffff;
  }
  * { box-sizing: border-box; margin: 0; padding: 0; }
  html, body {
    width: 1200px;
    height: 992px;
    overflow: hidden;
    background: var(--backdrop);
    font-family: "Source Sans 3", "Myriad Pro", Arial, sans-serif;
  }
  .canvas { position: relative; width: 1200px; height: 992px; }

  .card {
    position: absolute;
    top: 52px;
    width: 502px;
    height: 878px;
    overflow: hidden;
    box-shadow: 0 4px 14px rgba(0,0,0,0.25);
  }
  .card--front { left: 79px; background: var(--card-white); }
  .card--back { left: 622px; background: var(--slate); }

  /* Front: brand block */
  .brand {
    position: absolute;
    top: 40px;
    left: 56px;
    display: flex;
    align-items: center;
    gap: 18px;
  }
  .brand__mark {
    width: 96px;
    height: 96px;
    background: var(--slate);
  }
  .brand__name {
    color: var(--slate);
    font-weight: 700;
    font-size: 42px;
    line-height: 0.95;
    letter-spacing: 0.5px;
    text-transform: uppercase;
  }

  /* Front: person */
  .person {
    position: absolute;
    top: 462px;
    left: 0;
    width: 100%;
    text-align: center;
    color: var(--ink);
  }
  .person__name { font-weight: 700; font-size: 26px; color: var(--slate-dark); }
  .person__role { font-weight: 400; font-size: 21px; }

  .contacts {
    position: absolute;
    top: 530px;
    left: 0;
    width: 100%;
    list-style: none;
    font-size: 21px;
    color: var(--ink);
  }
  .contacts__row {
    display: flex;
    justify-content: center;
    align-items: center;
    gap: 8px;
    height: 36px;
  }
  .contacts__pair { display: inline-flex; align-items: center; gap: 8px; }
  .contacts__pair + .contacts__pair { margin-left: 14px; }
  .icon { width: 18px; height: 18px; flex: none; }

  .address {
    position: absolute;
    top: 704px;
    left: 0;
    width: 100%;
    text-align: center;
    font-size: 21px;
    color: var(--ink);
  }

  .footer-wave { position: absolute; left: 0; bottom: 0; width: 502px; height: 110px; }
  .tagline {
    position: absolute;
    left: 0;
    bottom: 16px;
    width: 100%;
    text-align: center;
    color: var(--light-text);
    font-size: 22px;
    letter-spacing: 3.5px;
    text-transform: uppercase;
  }

  /* Back */
  .back-brand {
    position: absolute;
    top: 370px;
    left: 0;
    width: 100%;
    text-align: center;
    color: var(--light-text);
    font-weight: 700;
    font-size: 56px;
    line-height: 1;
    letter-spacing: 1px;
    text-transform: uppercase;
  }
  .back-web {
    position: absolute;
    top: 810px;
    left: 0;
    width: 100%;
    text-align: center;
    color: var(--light-text);
    font-size: 25px;
    letter-spacing: 1.5px;
  }
  .back-web strong { font-weight: 600; }
</style>
</head>
<body>
<main class="canvas">

  <section class="card card--front" aria-label="Business card front">
    <div class="brand">
      <span class="brand__mark"></span>
      <div class="brand__name">Corvale<br>Networking</div>
    </div>

    <p class="person">
      <span class="person__name">Daniel Reyes,</span>
      <span class="person__role">Operation Manager</span>
    </p>

    <ul class="contacts">
      <li class="contacts__row">
        <span class="contacts__pair">
          <svg class="icon" viewBox="0 0 20 20" aria-hidden="true"><circle cx="10" cy="10" r="9" fill="none" stroke="#4a4f55" stroke-width="1.6"/><path d="M7 5.5c-1 1-1 3 1 5.5s4.5 3 5.5 2l-1.5-1.8-1.4.7c-.8-.4-2-1.7-2.3-2.5l.8-1.3z" fill="#4a4f55"/></svg>
          08 9355 1840
        </span>
        <span class="contacts__pair">
          <svg class="icon" viewBox="0 0 20 20" aria-hidden="true"><rect x="5" y="1" width="10" height="18" rx="1.5" fill="#4a4f55"/><rect x="6.5" y="3" width="7" height="6" fill="#fff"/><rect x="6.5" y="11" width="7" height="6" fill="#fff" opacity=".5"/></svg>
          0412 708 396
        </span>
      </li>
      <li class="contacts__row">
        <svg class="icon" viewBox="0 0 20 20" aria-hidden="true"><rect x="5" y="2" width="10" height="6" fill="#4a4f55"/><rect x="1" y="7" width="18" height="9" rx="1.5" fill="#4a4f55"/><rect x="5" y="12" width="10" height="6" fill="#fff" stroke="#4a4f55" stroke-width="1.4"/></svg>
        08 9355 1840
      </li>
      <li class="contacts__row">
        <svg class="icon" viewBox="0 0 20 20" aria-hidden="true"><path d="M2 8l8-5 8 5v9H2z" fill="#4a4f55"/><rect x="4.5" y="6" width="11" height="6" fill="#fff"/><path d="M2 8l8 6 8-6" fill="none" stroke="#fff" stroke-width="1.2"/></svg>
        daniel@corvalenetworking.com.au
      </li>
      <li class="contacts__row">
        <svg class="icon" viewBox="0 0 20 20" aria-hidden="true"><circle cx="10" cy="10" r="8.5" fill="none" stroke="#4a4f55" stroke-width="1.6"/><ellipse cx="10" cy="10" rx="3.5" ry="8.5" fill="none" stroke="#4a4f55" stroke-width="1.3"/><path d="M1.5 10h17M3 5.5h14M3 14.5h14" stroke="#4a4f55" stroke-width="1.2"/></svg>
        www.corvalenetworking.com.au
      </li>
    </ul>

    <p class="address">Unit 7 23 Marlowe Road, Bibra Lake WA 6163</p>

    <svg class="footer-wave" viewBox="0 0 502 110" preserveAspectRatio="none" aria-hidden="true">
      <path d="M0 30 C120 10 220 30 310 22 C390 14 450 8 502 12 L502 110 L0 110 Z" fill="#e4e7ea"/>
      <path d="M0 46 C120 22 230 40 320 30 C400 21 460 16 502 20" fill="none" stroke="#3f444a" stroke-width="3"/>
      <path d="M0 50 C120 32 240 50 330 42 C410 35 465 32 502 34 L502 110 L0 110 Z" fill="#627483"/>
    </svg>
    <p class="tagline">Complete IT Management</p>
  </section>

  <section class="card card--back" aria-label="Business card back">
    <div class="back-brand">Corvale<br>Networking</div>
    <p class="back-web">www.<strong>corvalenetworking</strong>.com.au</p>
  </section>

</main>
</body>
</html>
```